MRT Property - Business Cards

Looking for a business card & general letterhead, signage etc design for our new logo.

Colours:
000a20
0056a2
00b5ef
0088ce
68cef2

Fonts:
Poppins
Karla

Please keep look and feel of new brand - example in the zip package I sent.

```html
<!DOCTYPE html>
<html lang="en">
<head>
<meta charset="utf-8">
<title>MRT Property – Business Cards</title>
<link rel="stylesheet" href="https://fonts.googleapis.com/css2?family=Montserrat:wght@300;400&family=Poppins:wght@600&family=Gochi+Hand&display=swap">
<style>
  :root {
    --backdrop: #9a9a9a;
    --card: #121628;
    --card-deep: #0b0d18;
    --band: #0d58a8;
    --accent: #0088ce;
    --icon: #1f8fd0;
    --white: #ffffff;
    --text-soft: #e6e8ef;
    --pattern-light: #3c55a8;
  }
  * { box-sizing: border-box; margin: 0; padding: 0; }
  html, body {
    width: 1093px; height: 1200px; overflow: hidden;
    background: var(--backdrop);
  }
  .card {
    position: absolute; left: 265px; width: 580px; height: 363px;
    background: var(--card); border-radius: 18px; overflow: hidden;
  }
  .card--front { top: 225px; }
  .card--back { top: 616px; height: 366px; }
  .card__band {
    position: absolute; left: 0; right: 0; bottom: 0; height: 15px;
    background: var(--band);
  }
  .brand-name {
    position: absolute; left: 27px; top: 34px;
    font-family: "Poppins", sans-serif; font-weight: 600;
    font-size: 42px; line-height: 1; color: var(--white);
    letter-spacing: 0.5px;
  }
  .holder {
    position: absolute; right: 33px; top: 24px; text-align: right;
  }
  .holder__name {
    font-family: "Gochi Hand", cursive; font-size: 30px; line-height: 1;
    color: var(--accent);
  }
  .holder__title {
    font-family: "Montserrat", sans-serif; font-weight: 400;
    font-size: 13px; color: var(--text-soft); margin-top: 2px;
    letter-spacing: 0.3px;
  }
  .holder-tab {
    position: absolute; right: 0; top: 27px; width: 14px; height: 40px;
    background: var(--band);
  }
  .address {
    position: absolute; left: 31px; top: 199px;
    font-family: "Montserrat", sans-serif; font-weight: 300;
    font-size: 14px; line-height: 17px; color: var(--text-soft);
  }
  .contacts {
    position: absolute; left: 31px; top: 270px; list-style: none;
    font-family: "Montserrat", sans-serif; font-weight: 300;
    font-size: 14px; color: var(--text-soft);
  }
  .contacts li {
    display: flex; align-items: center; gap: 9px; height: 24.5px;
  }
  .contacts svg { width: 13px; height: 13px; fill: var(--icon); flex: none; }
  .front-decoration {
    position: absolute; left: 318px; top: 125px; width: 245px; height: 223px;
    background: radial-gradient(ellipse at 85% 20%, #2f3867 0%, #161a2f 45%, rgba(11,13,24,0.9) 75%, rgba(18,22,40,0) 100%);
    border-radius: 60% 30% 10% 50%;
  }
  .back-pattern {
    position: absolute; inset: 0 0 15px 0;
    background: linear-gradient(150deg, var(--pattern-light) 0%, #262c52 30%, #141830 55%, var(--card-deep) 100%);
  }
  .back-brand {
    position: absolute; left: 352px; top: 276px;
    display: flex; align-items: center; gap: 8px;
  }
  .back-brand__dot {
    width: 18px; height: 18px; border-radius: 50%; background: var(--accent);
  }
  .back-brand__name {
    font-family: "Poppins", sans-serif; font-weight: 600;
    font-size: 24px; line-height: 1; color: var(--white);
  }
</style>
</head>
<body>
  <section class="card card--front">
    <div class="brand-name">MRT Property</div>
    <div class="holder">
      <div class="holder__name">Daniel Reyes</div>
      <div class="holder__title">Managing Director</div>
    </div>
    <div class="holder-tab"></div>
    <div class="front-decoration" role="img" aria-label="Large faint brand symbol in dark navy tones"></div>
    <p class="address">240 Cedar Ridge Lane<br>Fairview, MS 39200</p>
    <ul class="contacts">
      <li>
        <svg viewBox="0 0 24 24" aria-hidden="true"><path d="M6.6 10.8a15.1 15.1 0 0 0 6.6 6.6l2.2-2.2c.3-.3.7-.4 1-.2 1.1.4 2.3.6 3.6.6.6 0 1 .4 1 1V20c0 .6-.4 1-1 1A17 17 0 0 1 3 4c0-.6.4-1 1-1h3.5c.6 0 1 .4 1 1 0 1.3.2 2.5.6 3.6.1.3 0 .7-.2 1z"/></svg>
        <span>555.014.2270</span>
      </li>
      <li>
        <svg viewBox="0 0 24 24" aria-hidden="true"><path d="M2 5h20v2l-10 6L2 7zM2 9l10 6 10-6v10H2z"/></svg>
        <span>info@mrtproperty.com</span>
      </li>
      <li>
        <svg viewBox="0 0 24 24" aria-hidden="true"><circle cx="12" cy="12" r="10"/></svg>
        <span>www.mrtproperty.com</span>
      </li>
    </ul>
    <div class="card__band"></div>
  </section>

  <section class="card card--back">
    <div class="back-pattern" role="img" aria-label="Repeating brand symbol pattern fading from blue to dark navy"></div>
    <div class="back-brand">
      <span class="back-brand__dot"></span>
      <span class="back-brand__name">MRT Property</span>
    </div>
    <div class="card__band"></div>
  </section>
</body>
</html>
```